Spring Exterior Painting Advertisement

Attached is the postcard that we used last year(file - pixelharbor_318939...vector....pdf.. The information contained will be the same except for it will be updated for use during the spring of 2023.

The second attachment (sept 2021mailer) is another design that we've used in the past.

```html
<!DOCTYPE html>
<html lang="en">
<head>
<meta charset="utf-8">
<title>Crestline Painting – Spring Postcard</title>
<link rel="stylesheet" href="https://fonts.googleapis.com/css2?family=Montserrat:wght@400;500;700;800;900&family=Dancing+Script:wght@500&display=swap">
<style>
  :root{
    --bg:#d6d7d9;
    --white:#ffffff;
    --ink:#1b1b1b;
    --maroon:#7b1a4b;
    --pink:#b0345f;
    --gold:#e6ac1e;
    --blue:#1d6a96;
    --blue-dark:#175a80;
    --sky:#9ec7ea;
    --grass:#5fae3a;
    --teal:#8fd1c0;
    --navy:#2a3470;
    --cyan:#4fb9dd;
    --green:#3d8f3f;
    --red:#d9482b;
    --violet:#a455a8;
  }
  *{box-sizing:border-box;margin:0;padding:0}
  html,body{width:1200px;height:2688px;overflow:hidden;background:var(--bg);font-family:"Montserrat",sans-serif}
  .card{position:absolute;left:100px;width:1000px;height:667px;background:var(--white);overflow:hidden;box-shadow:0 6px 18px rgba(0,0,0,.12)}
  .card--front{top:620px}
  .card--back{top:1400px}
  .card svg.art{position:absolute;left:0;top:0}
  .brand{position:absolute;font-family:"Montserrat",sans-serif;font-weight:800;color:var(--ink);letter-spacing:1px;line-height:1}
  .brand--front{left:50px;top:560px;font-size:46px}
  .brand--front small{display:block;font-size:22px;letter-spacing:11px;margin-top:6px}
  .brand--back{left:742px;top:95px;font-size:30px}
  .brand--back small{display:block;font-size:14px;letter-spacing:7px;margin-top:4px}
  .offer{position:absolute;left:545px;top:380px;width:390px;text-align:center;color:var(--white)}
  .offer__season{font-family:"Dancing Script",cursive;color:var(--gold);font-size:40px;line-height:1;position:relative;top:18px}
  .offer__save{font-weight:900;font-size:52px;line-height:1;letter-spacing:1px}
  .offer__amount{font-weight:900;color:var(--gold);font-size:140px;line-height:.95;letter-spacing:-4px}
  .offer__amount sup{font-size:62px;vertical-align:top;position:relative;top:10px;letter-spacing:0}
  .coupon{display:flex;justify-content:center;align-items:stretch;margin-top:10px}
  .coupon__label{background:var(--white);color:var(--maroon);font-weight:800;font-size:18px;line-height:1;padding:8px 12px;text-align:left}
  .coupon__code{border:2px dashed var(--gold);color:var(--white);font-weight:800;font-size:15px;padding:0 14px;display:flex;align-items:center}
  .banner{position:absolute;left:92px;top:42px;width:300px;height:104px;background:var(--pink);color:var(--white);padding:14px 0 0 50px;clip-path:polygon(2% 4%,100% 0,98% 30%,100% 62%,97% 100%,0 97%,2% 60%,0 30%)}
  .banner h2{font-weight:900;font-size:22px;line-height:1.1}
  .banner p{font-size:16px;line-height:1.2;font-weight:500}
  .roller{position:absolute;left:0;top:48px}
  .quote-title{position:absolute;left:48px;top:170px;color:var(--gold);font-weight:900;font-size:40px;line-height:1;letter-spacing:.5px}
  .quote-text{position:absolute;left:48px;top:262px;width:466px;font-size:13.5px;line-height:1.25;color:var(--ink);text-align:justify}
  .services{position:absolute;left:46px;top:324px;width:470px;height:212px;background:var(--blue);padding:22px 20px;display:grid;grid-template-columns:1fr 1.15fr;row-gap:14px;clip-path:polygon(0 2%,100% 0,99% 50%,100% 98%,1% 100%,0 50%)}
  .service{display:flex;align-items:center;color:var(--white);font-size:21px;line-height:.9}
  .service svg{flex:0 0 auto;margin-right:16px}
  .ba{position:absolute;width:72px;height:16px;border-radius:8px;background:var(--maroon);color:var(--white);font-size:10px;font-weight:700;text-align:center;line-height:16px}
  .ba--before{left:615px;top:302px}
  .ba--after{left:808px;top:302px}
  .contact{position:absolute;top:566px;display:flex;align-items:center;color:var(--blue)}
  .contact--phone{left:48px;font-weight:800;font-size:44px}
  .contact--web{left:540px;font-weight:500;font-size:28px}
  .contact svg{margin-right:14px}
  .stripes{position:absolute;left:46px;top:636px;width:900px;height:6px;display:flex;gap:2px}
  .stripes span{flex:1}
</style>
</head>
<body>

<section class="card card--front" aria-label="Postcard front">
  <svg class="art" width="1000" height="667" viewBox="0 0 1000 667">
    <defs>
      <linearGradient id="photoTone" x1="0" y1="0" x2="0" y2="1">
        <stop offset="0" stop-color="var(--sky)"/>
        <stop offset=".45" stop-color="#3f5aa6"/>
        <stop offset=".75" stop-color="#6b8fa8"/>
        <stop offset="1" stop-color="var(--grass)"/>
      </linearGradient>
    </defs>
    <path role="img" aria-label="Photo of a freshly painted blue two-storey house with a red roof, green lawn and flowering trees"
          d="M0 0H1000V460C860 500 700 520 560 515C360 508 160 420 0 330Z" fill="url(#photoTone)"/>
    <path d="M50 348C200 430 380 500 560 512C710 520 860 500 1000 462V484C860 522 700 542 560 538C370 528 190 460 40 372Z" fill="var(--blue)"/>
    <circle cx="735" cy="580" r="198" fill="var(--maroon)"/>
  </svg>
  <div class="brand brand--front">CRESTLINE<small>PAINTING</small></div>
  <div class="offer">
    <div class="offer__season">Spring</div>
    <div class="offer__save">SAVE</div>
    <div class="offer__amount">15<sup>%</sup></div>
    <div class="coupon">
      <div class="coupon__label">COUPON<br>CODE</div>
      <div class="coupon__code">“SPRINGEXT2023”</div>
    </div>
  </div>
</section>

<section class="card card--back" aria-label="Postcard back">
  <svg class="art" width="1000" height="667" viewBox="0 0 1000 667">
    <defs>
      <clipPath id="beforeClip"><circle cx="655" cy="425" r="92"/></clipPath>
    </defs>
    <circle role="img" aria-label="Before photo: empty white room with a ladder" cx="655" cy="425" r="92" fill="#e4e4e2"/>
    <circle role="img" aria-label="After photo: the same room painted mint green" cx="842" cy="425" r="98" fill="var(--teal)"/>
  </svg>
  <svg class="roller" width="100" height="70" viewBox="0 0 100 70" aria-hidden="true">
    <path d="M0 52H30L44 8H96" fill="none" stroke="#c9c9c9" stroke-width="4"/>
  </svg>
  <div class="banner">
    <h2>CRESTLINE PAINTING</h2>
    <p>18 Meadow Crest Rd. Unit B<br>Larkfield, WI 53099</p>
  </div>
  <div class="brand brand--back">CRESTLINE<small>PAINTING</small></div>
  <h1 class="quote-title">REQUEST YOUR<br>FREE CRESTLINE QUOTE</h1>
  <p class="quote-text">Crestline Painting's local team offers professional painting for your home's exterior and interior surfaces. With over 19 years in business, we offer skillful workmanship backed by a three-year warranty.</p>

  <div class="services">
    <div class="service"><svg width="32" height="32" viewBox="0 0 32 32"><rect x="8" y="6" width="16" height="22" rx="2" fill="none" stroke="var(--gold)" stroke-width="2"/></svg>Pressure<br>Washing</div>
    <div class="service"><svg width="32" height="32" viewBox="0 0 32 32"><path d="M4 16L16 5L28 16V28H4Z" fill="none" stroke="var(--gold)" stroke-width="2"/></svg>Exterior Painting<br>&amp; staining</div>
    <div class="service"><svg width="32" height="32" viewBox="0 0 32 32"><path d="M6 26L22 6M18 6H26V14" fill="none" stroke="var(--gold)" stroke-width="2"/></svg>Interior<br>Painting</div>
    <div class="service"><svg width="32" height="32" viewBox="0 0 32 32"><rect x="7" y="4" width="18" height="24" fill="none" stroke="var(--gold)" stroke-width="2"/><path d="M7 12H25M7 20H25" stroke="var(--gold)" stroke-width="2"/></svg>Cabinetry<br>inishing</div>
    <div class="service"><svg width="32" height="32" viewBox="0 0 32 32"><path d="M6 6L26 26M26 6L6 26" stroke="var(--gold)" stroke-width="2"/></svg>Carpentry</div>
    <div class="service"><svg width="32" height="32" viewBox="0 0 32 32"><rect x="4" y="14" width="24" height="14" fill="none" stroke="var(--gold)" stroke-width="2"/><path d="M8 14L14 4L20 14" fill="none" stroke="var(--gold)" stroke-width="2"/></svg>Color<br>Consultations</div>
  </div>

  <div class="ba ba--before">Before</div>
  <div class="ba ba--after">After</div>

  <div class="contact contact--phone">
    <svg width="20" height="26" viewBox="0 0 20 26"><path d="M6 2L10 8L7 11C8 15 11 19 14 21L17 18L19 23C16 26 11 25 7 19C3 13 2 6 6 2Z" fill="none" stroke="var(--gold)" stroke-width="2"/></svg>
    (555) 014-2290
  </div>
  <div class="contact contact--web">
    <svg width="26" height="26" viewBox="0 0 26 26"><circle cx="13" cy="13" r="11" fill="none" stroke="var(--gold)" stroke-width="2"/><ellipse cx="13" cy="13" rx="5" ry="11" fill="none" stroke="var(--gold)" stroke-width="2"/><path d="M2 13H24" stroke="var(--gold)" stroke-width="2"/></svg>
    CRESTLINEPAINTINGWI.COM
  </div>

  <div class="stripes" aria-hidden="true">
    <span style="background:var(--maroon)"></span>
    <span style="background:var(--gold)"></span>
    <span style="background:var(--teal)"></span>
    <span style="background:var(--navy)"></span>
    <span style="background:var(--cyan)"></span>
    <span style="background:var(--blue)"></span>
    <span style="background:var(--green)"></span>
    <span style="background:var(--red)"></span>
    <span style="background:var(--gold)"></span>
    <span style="background:var(--violet)"></span>
  </div>
</section>

</body>
</html>
```